Skincare Clinic specializing in treating difficult skin conditions needs a web design

We want to restructure and rehash our current webdesigns. The current ones are dated and look very old fashioned also, they are not structured well.

The current websites need to get an uplift in look and become more classy and modern with navigation ease by structuring the information into ease of access

The current web address is
www.brightdermhaven.com.au and
www.lumacutis.com.au

We also have international Partner website which is good and we need to better than them. So this website will act as a guide to better the new site
www.dermacalm-drtorvelle.com

But the new site should be more inclined towards a Blue colour or Aqua marine blue orientation and it needs to be Scientific giving authenticity to the medical industry we operate in.

Attached is a webdesign framework and architecture we would want to adopt. It is a schematic diagram and you can creatively adopt based on what you want to propose.

The website needs to be coded and Should be coded in WordPress such that it helps with SEO activity and nexora promoline pickup.

We will need the necessary pictures and we could provide them or agree to by them from the designers source.

Target Market(s)

Patients with Skin Disease and people interested to book consultation or buy products for their Skin condition

Industry/Entity Type

Clinic

Coding

Coded - Design and coding required

Number of Pages Required

5+ page

Font styles to use
Other font styles liked:
• Use a light font denoting class.

Requirements
Must have
• Should be modern, Easy to navigate, mobile friendly and coded in wordpress
• Blue colour and should look scientific and medicinal
Nice to have
• Classy and creative
Should not have
• No Green colour or herbal look

```html
<!DOCTYPE html>
<html lang="en">
<head>
<meta charset="utf-8">
<title>brightdermhaven – Lumacutis Skin Clinic</title>
<link href="https://fonts.googleapis.com/css2?family=Open+Sans:wght@400;600;700;800&display=swap" rel="stylesheet">
<style>
:root{
  --aqua:#33c0dd;
  --aqua-deep:#1aa8d6;
  --sky:#bfe9f5;
  --panel:#e0edf1;
  --panel-grey:#e3e9ec;
  --ink:#1b1b1b;
  --text:#2d2d2d;
  --link:#2fb4dc;
  --footer:#348fba;
  --footer-base:#28749b;
  --footer-text:#cfe7f2;
  --footer-divide:#4aa0c8;
  --white:#ffffff;
}
*{margin:0;padding:0;box-sizing:border-box}
html,body{width:1097px;height:1200px;overflow:hidden;background:var(--white)}
body{position:relative;font-family:"Open Sans",sans-serif;color:var(--text)}
.abs{position:absolute}

/* header */
.brand{left:101px;top:24px;display:flex;align-items:center;gap:10px}
.brand-name{font-size:30px;font-weight:600;color:var(--aqua);line-height:1;letter-spacing:-.5px}
.brand-sub{font-size:15px;font-weight:600;color:#4b5560;margin-top:3px;letter-spacing:-.3px}
.brand-mark{width:44px;height:44px;border-radius:50%;background:var(--aqua-deep)}
.tagline{left:466px;top:13px;width:530px;height:84px;background:linear-gradient(90deg,#39bdea 0%,#52c6ee 55%,#8fd7ef 100%);padding:14px 0 0 47px;color:var(--white)}
.tagline .q{position:absolute;left:24px;top:2px;font-size:24px;font-weight:800}
.tagline p{font-size:14.5px;font-weight:700;line-height:17px}
.tagline strong{display:block;font-size:25px;font-weight:800;color:#fff;line-height:28px;letter-spacing:.3px}

/* nav */
.main-nav{left:97px;top:99px;width:899px;height:44px;border:3px solid #a9e2f0;background:var(--aqua);display:flex;align-items:center;justify-content:space-around;padding:0 12px}
.main-nav a{font-size:14px;color:var(--white);text-decoration:none;padding:5px 20px}
.main-nav a.is-active{background:#b4e3ee;color:#1d3e4b}

/* hero */
.hero{left:97px;top:147px;width:899px;height:231px;border:4px solid #9fe0ef;background:linear-gradient(90deg,#ddd2c7 0%,#e6ddd3 55%,#efe9e3 100%);overflow:hidden}
.hero-photo{position:absolute;right:40px;top:0;width:290px;height:223px;background:radial-gradient(ellipse at 55% 45%,#c89a7f 0%,#b6876c 45%,#e4dbd2 78%)}
.hero-copy{position:absolute;left:23px;top:98px;font-size:20.5px;line-height:26px;color:var(--ink)}
.hero-copy strong{font-weight:800;font-size:20.5px;letter-spacing:.2px}
.hero-dots{position:absolute;right:10px;top:146px;display:flex;flex-direction:column;gap:6px}
.hero-dots span{width:9px;height:9px;border:1px solid var(--aqua);border-radius:50%;background:var(--white)}
.hero-dots span.on{background:var(--aqua-deep);border-color:var(--aqua-deep)}

/* services */
.services{left:97px;top:395px;width:899px;height:156px;background:var(--sky)}
.service{position:absolute;top:14px;width:228px;height:126px;background:var(--white);text-align:center;padding-top:11px}
.service.is-primary{background:var(--aqua)}
.service .ico{width:48px;height:48px;border-radius:50%;background:#bfc5c8;margin:0 auto;display:flex;align-items:center;justify-content:center}
.service.is-primary .ico{background:#dff6fb}
.service h3{font-size:11.5px;font-weight:700;color:var(--ink);margin-top:10px;letter-spacing:.2px}
.service p{font-size:21px;color:var(--ink);line-height:24px;letter-spacing:.3px}

/* founder */
.founder{left:97px;top:574px;width:432px;height:187px;background:var(--panel)}
.founder-photo{position:absolute;left:7px;top:16px;width:147px;height:146px;background:linear-gradient(180deg,#f3f3f3 0%,#c9a890 35%,#5b5d62 70%,#3e4045 100%)}
.founder-copy{position:absolute;left:176px;top:62px;width:240px}
.founder-copy h4{font-size:12.5px;font-weight:700;color:var(--ink)}
.founder-copy p{font-size:12px;line-height:19px;margin-top:8px;color:var(--ink)}
.founder-copy a{display:block;margin-top:5px;font-size:12.5px;color:var(--link);text-decoration:none}

/* case studies */
.cases{left:548px;top:574px;width:448px;height:187px;background:var(--panel)}
.cases-head{position:absolute;left:0;top:0;width:448px;height:46px}
.cases-title{position:absolute;left:175px;top:14px;font-size:15.5px;font-weight:800;color:var(--white);display:flex;gap:10px;align-items:center}
.cases-copy{position:absolute;left:23px;top:71px;width:200px;font-size:10.5px;line-height:15.5px;color:var(--ink)}
.btn{position:absolute;left:23px;top:157px;background:#22aee8;color:#0d2a3a;font-size:11.5px;padding:4px 8px;border-radius:3px}
.ba-label{position:absolute;top:51px;font-size:15.5px;color:var(--ink)}
.ba-photo{position:absolute;top:75px;width:101px;height:92px}
.ba-before{left:227px;background:radial-gradient(circle at 50% 50%,#d99d88 0%,#c97f6e 60%,#7a4a3a 100%)}
.ba-after{left:336px;background:radial-gradient(circle at 50% 50%,#f3d1c4 0%,#e5b6a6 60%,#a6736a 100%)}

/* testimonial */
.testimonial{left:180px;top:816px;width:737px;height:101px;background:var(--panel-grey);border-radius:3px;text-align:center}
.arrows{position:absolute;left:12px;top:10px;display:flex;gap:6px}
.testimonial h5{position:absolute;left:0;right:0;top:39px;font-size:12.5px;font-weight:600;color:#2190b8}
.testimonial blockquote{position:absolute;left:40px;right:40px;top:61px;font-size:10.5px;line-height:15.5px;color:var(--ink)}
.bubble{left:476px;top:787px}

/* footer */
.site-footer{left:0;top:936px;width:1097px;height:217px;background:var(--footer)}
.f-col{position:absolute;top:0;height:200px;padding-top:22px}
.f-col+.f-col{border-left:1px solid var(--footer-divide)}
.f-col h6{font-size:12.5px;font-weight:400;color:#e3f2f9;margin-bottom:16px}
.f-col li{list-style:none;font-size:10.5px;color:var(--footer-text);line-height:20.5px;padding-left:11px;position:relative}
.f-col li::before{content:"›";position:absolute;left:0;top:-1px;font-weight:700;font-size:13px}
.f-col li.plain::before{content:none}
.f-col li.hot{color:var(--white)}
.footer-base{left:0;top:1153px;width:1097px;height:47px;background:var(--footer-base);font-size:10.5px;color:#bcd6e4}
.footer-base .left{position:absolute;left:97px;top:17px}
.footer-base .right{position:absolute;right:98px;top:17px}
.socials{position:absolute;left:499px;top:12px;display:flex;gap:5px}
.socials span{width:20px;height:20px;background:#e9eef1;border:1px solid #334}
</style>
</head>
<body>

<header>
  <div class="abs brand">
    <div>
      <div class="brand-name">brightdermhaven</div>
      <div class="brand-sub">by Lumacutis Skin Clinic</div>
    </div>
    <span class="brand-mark"></span>
  </div>
  <div class="abs tagline">
    <span class="q">“</span>
    <p>BE EVERYWHERE,<br>DOEVERYTHING,AND NEVER FAIL TO<strong>THE CUSTOMER</strong></p>
  </div>
  <nav class="abs main-nav">
    <a href="#">About Us</a>
    <a href="#" class="is-active">Treatments</a>
    <a href="#">Products</a>
    <a href="#">Results</a>
    <a href="#">Media Skin</a>
    <a href="#">Conditions</a>
  </nav>
</header>

<section class="abs hero">
  <div class="hero-photo" role="img" aria-label="Photo of a young woman covering her mouth with her hands"></div>
  <div class="hero-copy">EMBARASSED<br>YOUR SKIN CONDITION?<br><strong>YOUR FATURE IS CLEAR WITH US,NATURALLY</strong></div>
  <div class="hero-dots"><span></span><span></span><span class="on"></span><span></span><span></span></div>
</section>

<section class="abs services">
  <div class="service is-primary" style="left:50px">
    <div class="ico"><svg width="24" height="24" viewBox="0 0 24 24" fill="none" stroke="#123" stroke-width="2"><path d="M5 3v6a4 4 0 0 0 8 0V3M9 13v3a4 4 0 0 0 8 0v-2"/><circle cx="17" cy="11" r="2"/></svg></div>
    <h3>CONSULTATION</h3><p>BOOK ONLINE</p>
  </div>
  <div class="service" style="left:332px">
    <div class="ico"><svg width="22" height="20" viewBox="0 0 22 20"><rect x="1" y="5" width="20" height="14" rx="1" fill="#111"/><rect x="7" y="1" width="8" height="5" fill="none" stroke="#111" stroke-width="2"/><path d="M11 16l-3-3a2 2 0 0 1 3-2 2 2 0 0 1 3 2z" fill="#fff"/></svg></div>
    <h3>PURCHASE</h3><p>PRODUCTS ONLINE</p>
  </div>
  <div class="service" style="left:614px">
    <div class="ico"><svg width="24" height="20" viewBox="0 0 24 20" stroke="#111" stroke-width="1.6"><path d="M2 10h2M6 7v6M9 4v12M12 1v18M15 5v10M18 8v4M21 10h2"/></svg></div>
    <h3>PRACTITIONERS</h3><p>INTRANET ACCESS</p>
  </div>
</section>

<section class="abs founder">
  <div class="founder-photo" role="img" aria-label="Portrait photo of the clinic founder in a suit"></div>
  <div class="founder-copy">
    <h4>Dr Adrian Velcourt</h4>
    <p>Medical Research Scientist and Founder of Lumacutis Skin Clinic, with clinics located throughout Australia and New Zealand.</p>
    <a href="#">READ MORE</a>
  </div>
</section>

<section class="abs cases">
  <svg class="cases-head" viewBox="0 0 448 46" preserveAspectRatio="none"><path d="M0 0H448V46H22L0 90Z" fill="#33c0dd"/></svg>
  <svg class="abs" style="left:0;top:46px" width="24" height="44"><path d="M0 0H22L0 44Z" fill="#33c0dd"/></svg>
  <div class="cases-title">
    <svg width="20" height="20" viewBox="0 0 20 20"><path d="M2 18l1-5L14 2l4 4L7 17z" fill="#111"/></svg>
    CASE STUDIES
  </div>
  <p class="cases-copy">These before and after photographs have been taken at the time of patient consultations and record the progress of the patient’s response to the treat-ment protocols.</p>
  <span class="btn">MORE GALLERY</span>
  <span class="ba-label" style="left:249px">Before</span>
  <span class="ba-label" style="left:366px">After</span>
  <div class="ba-photo ba-before" role="img" aria-label="Close-up photo of skin before treatment"></div>
  <div class="ba-photo ba-after" role="img" aria-label="Close-up photo of skin after treatment"></div>
</section>

<section class="abs testimonial">
  <div class="arrows">
    <svg width="18" height="14"><path d="M0 4h9V0l9 7-9 7v-4H0z" fill="#2fb4dc"/></svg>
    <svg width="18" height="14"><path d="M18 4H9V0L0 7l9 7v-4h9z" fill="#2fb4dc"/></svg>
  </div>
  <h5>P.O, Victoria, Australia</h5>
  <blockquote>"I've had psoriasis for over 25 years and used all the recommended forms of treatment. After using Dr. Velcourt's within three weeks I was well on my way to being psoriasis free."</blockquote>
</section>
<svg class="abs bubble" width="120" height="56" viewBox="0 0 120 56">
  <path d="M2 54A58 52 0 0 1 118 54L60 48Z" fill="#c9d1d5"/>
  <g fill="#111"><circle cx="60" cy="25" r="5"/><path d="M50 40a10 9 0 0 1 20 0z"/><circle cx="50" cy="27" r="4"/><path d="M42 40a8 7 0 0 1 14 0z"/><circle cx="70" cy="27" r="4"/><path d="M64 40a8 7 0 0 1 14 0z"/></g>
</svg>

<footer>
  <div class="abs site-footer">
    <div class="f-col" style="left:99px;width:165px"><h6>About Us</h6><ul>
      <li>Introduction</li><li>History</li><li>Our Founder</li><li>Our Treatment Protocol</li><li>Our Logo</li><li>International Partnership</li><li>Contact Details</li></ul></div>
    <div class="f-col" style="left:264px;width:203px;padding-left:27px"><h6>Treatment Protocol</h6><ul>
      <li>What do we specialise on</li><li>Consultations</li><li>5 Unique steps involved</li><li class="hot">Book an appointment</li><li>Clinic Location</li><li>Practitioners and associates</li><li>Cost of Consultation</li></ul></div>
    <div class="f-col" style="left:467px;width:207px;padding-left:27px"><h6>Products</h6><ul>
      <li>Introduction</li><li>Safety profile and test</li><li>Orals</li><li>Topicals</li><li>Others</li><li>Distributors</li><li>Distribution opportunities</li></ul></div>
    <div class="f-col" style="left:674px;width:181px;padding-left:24px"><h6>Results</h6><ul>
      <li>Clinical Trails</li><li>Case Studies</li><li>Before and After Photos</li><li>Patient Testimonials</li><li>Media exposure</li></ul></div>
    <div class="f-col" style="left:855px;width:160px;padding-left:15px"><h6>Skin Conditions</h6><ul>
      <li>Psoriasis</li><li>Eczema</li><li>Rosacea</li><li>Other Common</li><li class="plain">Skin conditions</li></ul></div>
  </div>
  <div class="abs footer-base">
    <span class="left">Disclaimer | Privacy</span>
    <div class="socials"><span></span><span></span><span></span></div>
    <span class="right">Copyright Pracitioner Login | Webmail</span>
  </div>
</footer>

</body>
</html>
```